Silver Harbor Med Spa Membership Sales Presentation to Clients handout

Hello! We are a high tech, Silver Harbor Med Spa in Dallas Texas that won Best Med Spa in Addison. I want my graphic membership form to represent that. We serve women and men so want it neutral but show cutting edge. Our colors are black, white, gray but would entertain your view. Having a challenge on making it easy to read as each membership gets more services yet one service a month. Thought maybe colorcoding what services are together? Definite road blocks on my end. I used Canva to lay out, but as you can see I am NOT gifted at graphic design. ;))

Target Market(s)

39-69

Industry/Entity Type

Medical Med Spa

Requirements
Must have
• cutting edge look

```html
<!DOCTYPE html>
<html lang="en">
<head>
<meta charset="utf-8">
<title>Forever Young Memberships – Silver Harbor Med Spa</title>
<link rel="stylesheet" href="https://fonts.googleapis.com/css2?family=Poppins:ital,wght@0,400;0,500;0,600;0,700;0,800;1,800;1,900&display=swap">
<style>
:root{
  --page:#e6e6e6;
  --ink:#000;
  --text:#1e1e1e;
  --white:#fff;
  --red:#e0101e;
  --good:#b3001b;
  --better:#17a06a;
  --best:#4b0ea3;
  --teal:#1fb8c8;
  --row-a:#ececec;
  --row-b:#f8f8f8;
  --cell-a:#d8d8d8;
  --cell-b:#ececec;
  --dot-green:#1d9c3c;
  --dot-blue:#2a6fd2;
  --purple:#9a1fd8;
  --blue:#1a7fe0;
  --navy:#1a1ab5;
  --violet:#8a10d2;
  --wl-head:#d4ebc6;
  --wl-a:#eef7e9;
  --wl-b:#dcefd2;
  --wl-title:#3e8a12;
  --off-10:#3aa63a;
  --off-20:#2e8a2e;
  --off-30:#1b451b;
}
*{box-sizing:border-box;margin:0;padding:0}
html,body{width:1200px;height:2400px;overflow:hidden;background:var(--page);font-family:"Poppins",sans-serif;color:var(--text)}
.sheet{position:absolute;left:50px;top:488px;width:950px;height:1230px;background:var(--white);transform:scale(1.15789);transform-origin:0 0;box-shadow:0 6px 18px rgba(0,0,0,.35);overflow:hidden}
.header-art,.footer-art{position:absolute;left:0;width:950px}
.header-art{top:0;height:205px}
.footer-art{top:1130px;height:100px}
.brand{position:absolute;left:35px;top:148px;width:200px;text-align:center;color:var(--white);font-size:14px;font-weight:500;letter-spacing:.5px}
.brand::before{content:"";display:block;width:10px;height:10px;border-radius:50%;background:var(--white);margin:0 auto 8px}
.title{position:absolute;left:335px;top:98px;font-style:italic;font-weight:900;font-size:41px;line-height:40px;letter-spacing:1px}
.title .l1{color:var(--ink);display:block}
.title .l2{color:var(--red);display:block}
.badge{position:absolute;left:736px;top:48px;width:158px;height:158px}

.table{position:absolute;left:32px;top:236px;width:883px}
.row{display:grid;grid-template-columns:428px 138px 138px 138px;column-gap:13px}
.head{height:56px;margin-bottom:2px}
.head .label{background:var(--ink);border-radius:6px 6px 0 0;padding:6px 0 0 26px}
.head .label h2{color:var(--teal);font-size:21px;font-weight:800;letter-spacing:6px;line-height:24px}
.head .label p{color:var(--white);font-size:12.5px;letter-spacing:.5px;margin-top:4px}
.tier{border-radius:6px 6px 0 0;color:var(--white);text-align:center;font-weight:700;font-size:19px;line-height:20px;padding-top:8px}
.tier.good{background:var(--good)}.tier.better{background:var(--better)}.tier.best{background:var(--best)}
.line{height:25.3px}
.line>div{display:flex;align-items:center}
.line .name{padding-left:26px;font-size:13.5px;letter-spacing:1px;text-transform:uppercase;background:var(--row-b)}
.line:nth-child(even) .name{background:var(--row-a)}
.line .cell{justify-content:center;background:var(--cell-b)}
.line:nth-child(even) .cell{background:var(--cell-a)}
.line:last-child>div{border-radius:0 0 6px 6px}
.name.plain{text-transform:none;letter-spacing:.3px;font-size:14px}
.name.hl{font-weight:700;letter-spacing:.5px;font-size:13.5px;padding-left:28px}
.hl.purple{color:var(--purple)}.hl.blue{color:var(--blue)}.hl.red{color:var(--red)}.hl.navy{color:var(--navy)}.hl.violet{color:var(--violet)}
.dot{width:11px;height:11px;border-radius:50%;border:2px solid currentColor;margin-right:14px;position:relative;flex:none}
.dot::after{content:"";position:absolute;inset:1.5px;border-radius:50%;background:currentColor}
.dot.g{color:var(--dot-green)}.dot.b{color:var(--dot-blue)}
.tick{width:15px;height:15px}
.c-good{color:var(--good)}.c-better{color:var(--better)}.c-best{color:var(--best)}

.weight{position:absolute;left:32px;top:795px;width:883px}
.weight .whead{height:50px}
.weight .whead>div{background:var(--wl-head);border-radius:8px 8px 0 0}
.weight .whead .wtitle{color:var(--wl-title);font-weight:700;font-size:16px;letter-spacing:1px;padding:18px 0 0 28px}
.wline{height:28.8px}
.wline>div{display:flex;align-items:center;background:var(--wl-a)}
.wline:nth-child(odd)>div{background:var(--wl-b)}
.wline:last-child>div{border-radius:0 0 8px 8px}
.wline .name{padding-left:30px;font-size:13px;letter-spacing:.6px;text-transform:uppercase}
.wline .name .dot{color:var(--dot-green);margin-right:17px}
.wline .off{justify-content:center;font-size:15.5px;letter-spacing:.5px}
.off.o10{color:var(--off-10)}.off.o20{color:var(--off-20)}.off.o30{color:var(--off-30)}

.contact{position:absolute;left:45px;top:1146px;width:860px;height:82px;display:flex;align-items:center;color:var(--white);font-size:16.5px;font-weight:500}
.contact .item{display:flex;align-items:center;gap:8px}
.contact .sep{width:2px;height:22px;background:var(--white);margin:0 26px}
.contact svg{width:17px;height:17px}
</style>
</head>
<body>
<div class="sheet">
  <svg class="header-art" viewBox="0 0 950 205" aria-hidden="true">
    <polygon points="0,0 950,0 950,68 331,68 246,205 0,205" fill="var(--ink)"/>
    <polygon points="331,68 950,68 950,88 344,88 267,205 246,205" fill="var(--red)"/>
  </svg>
  <div class="brand">Silver Harbor Med Spa</div>
  <h1 class="title"><span class="l1">FOREVER YOUNG</span><span class="l2">MEMBERSHIPS</span></h1>
  <svg class="badge" viewBox="0 0 158 158" role="img" aria-label="Award badge">
    <circle cx="79" cy="79" r="77" fill="var(--red)"/>
    <circle cx="79" cy="79" r="71" fill="var(--ink)"/>
    <circle cx="79" cy="79" r="56" fill="#7a0010"/>
  </svg>

  <section class="table">
    <div class="row head">
      <div class="label"><h2>TREATMENTS</h2><p>GREEN UNLIMITED/CHOSE ONE COLOR PER MONTH ‘</p></div>
      <div class="tier good">GOOD<br>$189</div>
      <div class="tier better">BETTER<br>$289</div>
      <div class="tier best">BEST<br>$389</div>
    </div>
    <div class="rows">
      <div class="row line"><div class="name"><span class="dot g"></span>Skin Evaluation</div><div class="cell c-good"><svg class="tick" viewBox="0 0 16 16"><circle cx="8" cy="8" r="8" fill="currentColor"/><path d="M4.5 8.3l2.3 2.3 4.7-4.9" stroke="#fff" stroke-width="1.8" fill="none"/></svg></div><div class="cell c-better"><svg class="tick" viewBox="0 0 16 16"><circle cx="8" cy="8" r="8" fill="currentColor"/><path d="M4.5 8.3l2.3 2.3 4.7-4.9" stroke="#fff" stroke-width="1.8" fill="none"/></svg></div><div class="cell c-best"><svg class="tick" viewBox="0 0 16 16"><circle cx="8" cy="8" r="8" fill="currentColor"/><path d="M4.5 8.3l2.3 2.3 4.7-4.9" stroke="#fff" stroke-width="1.8" fill="none"/></svg></div></div>
      <div class="row line"><div class="name"><span class="dot g"></span>Infrared Sauna</div><div class="cell c-good"><svg class="tick" viewBox="0 0 16 16"><circle cx="8" cy="8" r="8" fill="currentColor"/><path d="M4.5 8.3l2.3 2.3 4.7-4.9" stroke="#fff" stroke-width="1.8" fill="none"/></svg></div><div class="cell c-better"><svg class="tick" viewBox="0 0 16 16"><circle cx="8" cy="8" r="8" fill="currentColor"/><path d="M4.5 8.3l2.3 2.3 4.7-4.9" stroke="#fff" stroke-width="1.8" fill="none"/></svg></div><div class="cell c-best"><svg class="tick" viewBox="0 0 16 16"><circle cx="8" cy="8" r="8" fill="currentColor"/><path d="M4.5 8.3l2.3 2.3 4.7-4.9" stroke="#fff" stroke-width="1.8" fill="none"/></svg></div></div>
      <div class="row line"><div class="name"><span class="dot g"></span>Massage Chair</div><div class="cell c-good"><svg class="tick" viewBox="0 0 16 16"><circle cx="8" cy="8" r="8" fill="currentColor"/><path d="M4.5 8.3l2.3 2.3 4.7-4.9" stroke="#fff" stroke-width="1.8" fill="none"/></svg></div><div class="cell c-better"><svg class="tick" viewBox="0 0 16 16"><circle cx="8" cy="8" r="8" fill="currentColor"/><path d="M4.5 8.3l2.3 2.3 4.7-4.9" stroke="#fff" stroke-width="1.8" fill="none"/></svg></div><div class="cell c-best"><svg class="tick" viewBox="0 0 16 16"><circle cx="8" cy="8" r="8" fill="currentColor"/><path d="M4.5 8.3l2.3 2.3 4.7-4.9" stroke="#fff" stroke-width="1.8" fill="none"/></svg></div></div>
      <div class="row line"><div class="name"><span class="dot g"></span>Vibrational Lymphatic Plate</div><div class="cell c-good"><svg class="tick" viewBox="0 0 16 16"><circle cx="8" cy="8" r="8" fill="currentColor"/><path d="M4.5 8.3l2.3 2.3 4.7-4.9" stroke="#fff" stroke-width="1.8" fill="none"/></svg></div><div class="cell c-better"><svg class="tick" viewBox="0 0 16 16"><circle cx="8" cy="8" r="8" fill="currentColor"/><path d="M4.5 8.3l2.3 2.3 4.7-4.9" stroke="#fff" stroke-width="1.8" fill="none"/></svg></div><div class="cell c-best"><svg class="tick" viewBox="0 0 16 16"><circle cx="8" cy="8" r="8" fill="currentColor"/><path d="M4.5 8.3l2.3 2.3 4.7-4.9" stroke="#fff" stroke-width="1.8" fill="none"/></svg></div></div>
      <div class="row line"><div class="name"><span class="dot b"></span>Medical Facial</div><div class="cell c-good"><svg class="tick" viewBox="0 0 16 16"><circle cx="8" cy="8" r="8" fill="currentColor"/><path d="M4.5 8.3l2.3 2.3 4.7-4.9" stroke="#fff" stroke-width="1.8" fill="none"/></svg></div><div class="cell c-better"><svg class="tick" viewBox="0 0 16 16"><circle cx="8" cy="8" r="8" fill="currentColor"/><path d="M4.5 8.3l2.3 2.3 4.7-4.9" stroke="#fff" stroke-width="1.8" fill="none"/></svg></div><div class="cell c-best"><svg class="tick" viewBox="0 0 16 16"><circle cx="8" cy="8" r="8" fill="currentColor"/><path d="M4.5 8.3l2.3 2.3 4.7-4.9" stroke="#fff" stroke-width="1.8" fill="none"/></svg></div></div>
      <div class="row line"><div class="name"><span class="dot b"></span>Face Lymphatic Drainage</div><div class="cell c-good"><svg class="tick" viewBox="0 0 16 16"><circle cx="8" cy="8" r="8" fill="currentColor"/><path d="M4.5 8.3l2.3 2.3 4.7-4.9" stroke="#fff" stroke-width="1.8" fill="none"/></svg></div><div class="cell c-better"><svg class="tick" viewBox="0 0 16 16"><circle cx="8" cy="8" r="8" fill="currentColor"/><path d="M4.5 8.3l2.3 2.3 4.7-4.9" stroke="#fff" stroke-width="1.8" fill="none"/></svg></div><div class="cell c-best"><svg class="tick" viewBox="0 0 16 16"><circle cx="8" cy="8" r="8" fill="currentColor"/><path d="M4.5 8.3l2.3 2.3 4.7-4.9" stroke="#fff" stroke-width="1.8" fill="none"/></svg></div></div>
      <div class="row line"><div class="name"><span class="dot b"></span>Red Light Therapy</div><div class="cell c-good"><svg class="tick" viewBox="0 0 16 16"><circle cx="8" cy="8" r="8" fill="currentColor"/><path d="M4.5 8.3l2.3 2.3 4.7-4.9" stroke="#fff" stroke-width="1.8" fill="none"/></svg></div><div class="cell c-better"><svg class="tick" viewBox="0 0 16 16"><circle cx="8" cy="8" r="8" fill="currentColor"/><path d="M4.5 8.3l2.3 2.3 4.7-4.9" stroke="#fff" stroke-width="1.8" fill="none"/></svg></div><div class="cell c-best"><svg class="tick" viewBox="0 0 16 16"><circle cx="8" cy="8" r="8" fill="currentColor"/><path d="M4.5 8.3l2.3 2.3 4.7-4.9" stroke="#fff" stroke-width="1.8" fill="none"/></svg></div></div>
      <div class="row line"><div class="name"><span class="dot b"></span>PH Oxygen Serum</div><div class="cell c-good"><svg class="tick" viewBox="0 0 16 16"><circle cx="8" cy="8" r="8" fill="currentColor"/><path d="M4.5 8.3l2.3 2.3 4.7-4.9" stroke="#fff" stroke-width="1.8" fill="none"/></svg></div><div class="cell c-better"><svg class="tick" viewBox="0 0 16 16"><circle cx="8" cy="8" r="8" fill="currentColor"/><path d="M4.5 8.3l2.3 2.3 4.7-4.9" stroke="#fff" stroke-width="1.8" fill="none"/></svg></div><div class="cell c-best"><svg class="tick" viewBox="0 0 16 16"><circle cx="8" cy="8" r="8" fill="currentColor"/><path d="M4.5 8.3l2.3 2.3 4.7-4.9" stroke="#fff" stroke-width="1.8" fill="none"/></svg></div></div>
      <div class="row line"><div class="name hl purple" style="padding-left:26px">CHEMICAL PEELS PROGRESSIVE OR MIDDEPTH</div><div class="cell c-good"><svg class="tick" viewBox="0 0 16 16"><circle cx="8" cy="8" r="8" fill="currentColor"/><path d="M4.5 8.3l2.3 2.3 4.7-4.9" stroke="#fff" stroke-width="1.8" fill="none"/></svg></div><div class="cell c-better"><svg class="tick" viewBox="0 0 16 16"><circle cx="8" cy="8" r="8" fill="currentColor"/><path d="M4.5 8.3l2.3 2.3 4.7-4.9" stroke="#fff" stroke-width="1.8" fill="none"/></svg></div><div class="cell c-best"><svg class="tick" viewBox="0 0 16 16"><circle cx="8" cy="8" r="8" fill="currentColor"/><path d="M4.5 8.3l2.3 2.3 4.7-4.9" stroke="#fff" stroke-width="1.8" fill="none"/></svg></div></div>
      <div class="row line"><div class="name plain">Lumora Light Youth Renewal</div><div class="cell c-good"><svg class="tick" viewBox="0 0 16 16"><circle cx="8" cy="8" r="8" fill="currentColor"/><path d="M4.5 8.3l2.3 2.3 4.7-4.9" stroke="#fff" stroke-width="1.8" fill="none"/></svg></div><div class="cell c-better"><svg class="tick" viewBox="0 0 16 16"><circle cx="8" cy="8" r="8" fill="currentColor"/><path d="M4.5 8.3l2.3 2.3 4.7-4.9" stroke="#fff" stroke-width="1.8" fill="none"/></svg></div><div class="cell c-best"><svg class="tick" viewBox="0 0 16 16"><circle cx="8" cy="8" r="8" fill="currentColor"/><path d="M4.5 8.3l2.3 2.3 4.7-4.9" stroke="#fff" stroke-width="1.8" fill="none"/></svg></div></div>
      <div class="row line"><div class="name plain">Lumora 2 Correction Passes</div><div class="cell c-good"><svg class="tick" viewBox="0 0 16 16"><circle cx="8" cy="8" r="8" fill="currentColor"/><path d="M4.5 8.3l2.3 2.3 4.7-4.9" stroke="#fff" stroke-width="1.8" fill="none"/></svg></div><div class="cell c-better"><svg class="tick" viewBox="0 0 16 16"><circle cx="8" cy="8" r="8" fill="currentColor"/><path d="M4.5 8.3l2.3 2.3 4.7-4.9" stroke="#fff" stroke-width="1.8" fill="none"/></svg></div><div class="cell c-best"><svg class="tick" viewBox="0 0 16 16"><circle cx="8" cy="8" r="8" fill="currentColor"/><path d="M4.5 8.3l2.3 2.3 4.7-4.9" stroke="#fff" stroke-width="1.8" fill="none"/></svg></div></div>
      <div class="row line"><div class="name"><span class="dot b"></span>Dermaplaning</div><div class="cell"></div><div class="cell c-better"><svg class="tick" viewBox="0 0 16 16"><circle cx="8" cy="8" r="8" fill="currentColor"/><path d="M4.5 8.3l2.3 2.3 4.7-4.9" stroke="#fff" stroke-width="1.8" fill="none"/></svg></div><div class="cell c-best"><svg class="tick" viewBox="0 0 16 16"><circle cx="8" cy="8" r="8" fill="currentColor"/><path d="M4.5 8.3l2.3 2.3 4.7-4.9" stroke="#fff" stroke-width="1.8" fill="none"/></svg></div></div>
      <div class="row line"><div class="name"><span class="dot b"></span>Vitamin A Peel</div><div class="cell"></div><div class="cell c-better"><svg class="tick" viewBox="0 0 16 16"><circle cx="8" cy="8" r="8" fill="currentColor"/><path d="M4.5 8.3l2.3 2.3 4.7-4.9" stroke="#fff" stroke-width="1.8" fill="none"/></svg></div><div class="cell c-best"><svg class="tick" viewBox="0 0 16 16"><circle cx="8" cy="8" r="8" fill="currentColor"/><path d="M4.5 8.3l2.3 2.3 4.7-4.9" stroke="#fff" stroke-width="1.8" fill="none"/></svg></div></div>
      <div class="row line"><div class="name plain">Lumora Up To 10 Correction Passes</div><div class="cell"></div><div class="cell c-better"><svg class="tick" viewBox="0 0 16 16"><circle cx="8" cy="8" r="8" fill="currentColor"/><path d="M4.5 8.3l2.3 2.3 4.7-4.9" stroke="#fff" stroke-width="1.8" fill="none"/></svg></div><div class="cell c-best"><svg class="tick" viewBox="0 0 16 16"><circle cx="8" cy="8" r="8" fill="currentColor"/><path d="M4.5 8.3l2.3 2.3 4.7-4.9" stroke="#fff" stroke-width="1.8" fill="none"/></svg></div></div>
      <div class="row line"><div class="name plain">Lumora Hair Removal</div><div class="cell"></div><div class="cell c-better"><svg class="tick" viewBox="0 0 16 16"><circle cx="8" cy="8" r="8" fill="currentColor"/><path d="M4.5 8.3l2.3 2.3 4.7-4.9" stroke="#fff" stroke-width="1.8" fill="none"/></svg></div><div class="cell c-best"><svg class="tick" viewBox="0 0 16 16"><circle cx="8" cy="8" r="8" fill="currentColor"/><path d="M4.5 8.3l2.3 2.3 4.7-4.9" stroke="#fff" stroke-width="1.8" fill="none"/></svg></div></div>
      <div class="row line"><div class="name hl blue">MICRONEEDLING</div><div class="cell"></div><div class="cell c-better"><svg class="tick" viewBox="0 0 16 16"><circle cx="8" cy="8" r="8" fill="currentColor"/><path d="M4.5 8.3l2.3 2.3 4.7-4.9" stroke="#fff" stroke-width="1.8" fill="none"/></svg></div><div class="cell c-best"><svg class="tick" viewBox="0 0 16 16"><circle cx="8" cy="8" r="8" fill="currentColor"/><path d="M4.5 8.3l2.3 2.3 4.7-4.9" stroke="#fff" stroke-width="1.8" fill="none"/></svg></div></div>
      <div class="row line"><div class="name hl red">LUMORA SKIN FIRM</div><div class="cell"></div><div class="cell"></div><div class="cell c-best"><svg class="tick" viewBox="0 0 16 16"><circle cx="8" cy="8" r="8" fill="currentColor"/><path d="M4.5 8.3l2.3 2.3 4.7-4.9" stroke="#fff" stroke-width="1.8" fill="none"/></svg></div></div>
      <div class="row line"><div class="name hl navy">MICRONEEDLING PDO BRIGHTLINE</div><div class="cell"></div><div class="cell"></div><div class="cell c-best"><svg class="tick" viewBox="0 0 16 16"><circle cx="8" cy="8" r="8" fill="currentColor"/><path d="M4.5 8.3l2.3 2.3 4.7-4.9" stroke="#fff" stroke-width="1.8" fill="none"/></svg></div></div>
      <div class="row line"><div class="name hl violet">CHEMICAL PEEL NIVRA ITALIAN</div><div class="cell"></div><div class="cell"></div><div class="cell c-best"><svg class="tick" viewBox="0 0 16 16"><circle cx="8" cy="8" r="8" fill="currentColor"/><path d="M4.5 8.3l2.3 2.3 4.7-4.9" stroke="#fff" stroke-width="1.8" fill="none"/></svg></div></div>
    </div>
  </section>

  <section class="weight">
    <div class="row whead"><div class="wtitle">VANTRA TARGETED WEIGHT LOSS</div><div></div><div></div><div></div></div>
    <div class="wrows">
      <div class="row wline"><div class="name"><span class="dot"></span>Laser Rejuvenaiio</div><div class="off o10">10% OFF</div><div class="off o20">20% OFF</div><div class="off o30">30% OFF</div></div>
      <div class="row wline"><div class="name"><span class="dot"></span>Plasma Pen</div><div class="off o10">10% OFF</div><div class="off o20">20% OFF</div><div class="off o30">30% OFF</div></div>
      <div class="row wline"><div class="name"><span class="dot"></span>Hyperbaric Oxygen</div><div class="off o10">10% OFF</div><div class="off o20">20% OFF</div><div class="off o30">30% OFF</div></div>
      <div class="row wline"><div class="name"><span class="dot"></span>Massage</div><div class="off o10">10% OFF</div><div class="off o20">20% OFF</div><div class="off o30">30% OFF</div></div>
      <div class="row wline"><div class="name"><span class="dot"></span>Airbrush Tanning</div><div class="off o10">10% OFF</div><div class="off o20">20% OFF</div><div class="off o30">30% OFF</div></div>
      <div class="row wline"><div class="name"><span class="dot"></span>Ionic Detox</div><div class="off o10">10% OFF</div><div class="off o20">20% OFF</div><div class="off o30">30% OFF</div></div>
      <div class="row wline"><div class="name"><span class="dot"></span>Lymphatic Drainage</div><div class="off o10">10% OFF</div><div class="off o20">20% OFF</div><div class="off o30">30% OFF</div></div>
      <div class="row wline"><div class="name"><span class="dot"></span>Tirzepatide Weight Loss Peptide</div><div class="off o10">10% OFF</div><div class="off o20">20% OFF</div><div class="off o30">30% OFF</div></div>
      <div class="row wline"><div class="name"><span class="dot"></span>Lip Fillers Needle-Less</div><div class="off o10">10% OFF</div><div class="off o20">20% OFF</div><div class="off o30">30% OFF</div></div>
    </div>
  </section>

  <svg class="footer-art" viewBox="0 1130 950 100" aria-hidden="true">
    <rect x="57" y="1136" width="833" height="6" fill="var(--red)"/>
    <polygon points="40,1146 910,1146 932,1230 18,1230" fill="var(--ink)"/>
    <polygon points="0,1200 14,1168 22,1168 7,1230 0,1230" fill="var(--red)"/>
    <polygon points="950,1200 936,1168 928,1168 943,1230 950,1230" fill="var(--red)"/>
  </svg>
  <div class="contact">
    <div class="item"><svg viewBox="0 0 16 16"><circle cx="8" cy="8" r="8" fill="var(--red)"/><path d="M8 3.2a3 3 0 0 0-3 3c0 2.3 3 6 3 6s3-3.7 3-6a3 3 0 0 0-3-3z" fill="#fff"/><circle cx="8" cy="6.2" r="1.1" fill="var(--red)"/></svg>1187 Larkspur Ave. Plano, TX 75000</div>
    <span class="sep"></span>
    <div class="item"><svg viewBox="0 0 16 16"><circle cx="8" cy="8" r="8" fill="var(--red)"/><path d="M5.2 4.2l1.6-.4 1 2.2-1 .8a5 5 0 0 0 2.4 2.4l.8-1 2.2 1-.4 1.6c-3.6.4-7-3-6.6-6.6z" fill="#fff"/></svg>214.555.0143</div>
    <span class="sep"></span>
    <div class="item"><svg viewBox="0 0 16 16"><circle cx="8" cy="8" r="7" fill="none" stroke="var(--red)" stroke-width="2"/><path d="M1 8h14M8 1v14" stroke="var(--red)" stroke-width="1.6"/></svg>www.SilverHarborMedSpa.com</div>
  </div>
</div>
</body>
</html>
```